Field Anchor - Design a new page for our website

The designer is to use our existing website to match color and style and the documents provided to create a webpage that reflects the information in the brochure attached. This should also include a button to download our brochure and a form to request more information by entering name, phone, and email. This page will be added to our main site and will be coded by our webmaster team.

View website at www.harrowfield.us

The successful designer will be asked to also design another page for additional compensation.

Target Market(s)

Security and Law Enforcement

Industry/Entity Type

Security Service

Coding

Number of Pages Required

1 page

Font styles to use
Other font styles liked:
• Raleway or match site font and style

Requirements
Must have
• Match in color and style to our existing site as this page will be added to the existing website.

UPDATE: Place FRB Logo (attached to the brief) in a horizontal bar the width of the page with the following text:

"Field Anchor and all of Harrowfield's services are available on under our FRB Contract." (Add button) Click for Info
Nice to have
• Simple design expressing clean and easy to comprehend points

Please be creative, use the ability to scroll vertically on the page to space out the content and add supporting graphics or images.

```html
<!DOCTYPE html>
<html lang="en">
<head>
<meta charset="utf-8">
<title>Harrowfield Consulting – Field Anchor Special Event Services</title>
<link href="https://fonts.googleapis.com/css2?family=Ubuntu:wght@400;500;700&family=Roboto:wght@400;700&display=swap" rel="stylesheet">
<style>
:root{
  --blue:#1a8fe3;
  --blue-dark:#0f6fb8;
  --ink:#1c1c1e;
  --text:#333;
  --muted:#6b6b6b;
  --canvas:#e2e2e2;
  --light:#efefef;
  --white:#fff;
}
*{box-sizing:border-box;margin:0;padding:0}
html,body{width:710px;height:1200px;overflow:hidden;background:var(--canvas)}
body{font-family:"Roboto",Arial,sans-serif;color:var(--text)}
.stage{position:absolute;left:0;top:0;width:1484px;height:2510px;transform:scale(.47844);transform-origin:0 0}
.page{position:absolute;top:73px;width:594px;background:var(--white);box-shadow:0 2px 10px rgba(0,0,0,.18);overflow:hidden}
.page--a{left:110px}
.page--b{left:780px}
section,header,footer{position:relative;width:594px}
.abs{position:absolute}

/* top bar */
.topbar{height:18px;background:var(--ink);color:#fff;font-size:5.4px}
.topbar .item{position:absolute;top:6px;display:flex;align-items:center;gap:3px}
.topbar .dot{width:4px;height:4px;border-radius:50%;background:var(--blue)}
.topbar .social{position:absolute;top:6px;left:500px;display:flex;gap:9px}
.topbar .social span{width:5px;height:5px;border-radius:50%;background:#fff}

/* nav */
.nav{height:42px;border-bottom:1px solid #eee}
.brand{position:absolute;left:55px;top:9px;display:flex;align-items:center;gap:5px;font-family:"Ubuntu",sans-serif;font-weight:500;font-size:15px;color:var(--ink)}
.brand .mark{width:14px;height:14px;border-radius:50%;background:var(--blue)}
.menu{position:absolute;left:198px;top:17px;display:flex;gap:11px;font-size:6.6px;color:#222}
.menu .active{color:var(--blue);position:relative}
.menu .active::after{content:"";position:absolute;left:0;right:0;bottom:-6px;height:1.5px;background:var(--blue)}
.btn{display:inline-flex;align-items:center;justify-content:center;gap:3px;background:var(--blue);color:#fff;border-radius:12px;font-weight:700;font-size:6.4px}
.nav .btn{position:absolute;left:443px;top:11px;width:95px;height:18px;font-weight:400}

/* hero */
.hero{background:linear-gradient(100deg,#5b6a4a 0%,#a9b38a 25%,#c9b89a 45%,#7f8b7d 65%,#3c4a52 100%)}
.page--a .hero{height:317px}
.page--b .hero{height:289px}
.hero-panel{position:absolute;left:144px;top:110px;width:304px;height:137px;background:rgba(18,18,20,.72);color:#fff;text-align:center}
.hero-panel h1{font-family:"Ubuntu",sans-serif;font-weight:500;font-size:18.5px;line-height:24px;margin-top:8px}
.hero-panel p{font-size:7px;margin-top:12px;letter-spacing:.1px}
.hero-panel .btn{width:116px;height:23px;margin-top:14px;border-radius:12px}
.hero-curve{position:absolute;left:0;bottom:0;width:594px;height:90px}

/* titles */
.title{position:absolute;left:0;width:594px;text-align:center;font-family:"Ubuntu",sans-serif;font-size:19px;color:var(--ink)}
.title b{color:var(--blue);font-weight:500}
.title--rule::after{content:"";display:block;width:42px;height:2px;background:#aaa;margin:6px auto 0}

/* security */
.security{background:linear-gradient(160deg,#f4f4f4,#e9e9e9 60%,#f2f2f2)}
.page--a .security{height:433px}
.page--b .security{height:440px}
.cards{position:absolute;left:55px;top:95px;width:483px;display:grid;grid-template-columns:repeat(3,152px);column-gap:14px;row-gap:17px}
.card{background:#fff;text-align:center;padding:13px 8px 0}
.cards .card:nth-child(-n+3){height:148px}
.cards .card:nth-child(n+4){height:128px}
.icon{display:flex;align-items:center;justify-content:center;border-radius:50%;background:var(--blue)}
.card .icon{width:38px;height:38px;margin:0 auto}
.icon i{display:block;width:40%;height:34%;border:1.5px solid #fff;border-radius:2px}
.card h3{font-size:7.6px;font-weight:700;color:#222;margin-top:10px}
.card p{font-size:6.2px;line-height:11.8px;color:var(--muted);margin-top:6px}

/* communication */
.comm{height:354px;background:#fff}
.comm .title{top:38px}
.comm-list{position:absolute;left:55px;top:88px;width:235px}
.comm-item{display:flex;gap:8px;margin-bottom:14px}
.comm-item .icon{flex:none;width:28px;height:28px;margin-top:2px}
.comm-item h4{font-size:7.4px;font-weight:700;color:#111;margin-bottom:5px}
.comm-item p{font-size:6.2px;line-height:11.5px;color:var(--muted)}
.comm-photo{position:absolute;left:318px;top:79px;width:220px;height:217px;background:linear-gradient(135deg,#e8edf2,#b8c6d6 55%,#6d7f96)}

/* split */
.split{height:235px;display:flex}
.page--b .split{height:234px}
.split .half{width:297px;height:100%;color:#fff;padding-top:26px}
.half--dark{background:var(--ink);padding-left:55px;padding-right:20px}
.half--blue{background:var(--blue);padding-left:17px;padding-right:34px}
.split-head{display:flex;gap:12px;align-items:flex-start}
.split-head .badge{flex:none;width:35px;height:35px;border-radius:50%;background:#fff;display:flex;align-items:center;justify-content:center}
.split-head .badge i{width:15px;height:12px;border:1.5px solid var(--ink);border-radius:2px}
.split-head h2{font-family:"Ubuntu",sans-serif;font-weight:500;font-size:12.5px;line-height:19px}
.half--dark h2 b{color:var(--blue);font-weight:500}
.half--blue h2{text-transform:none}
.split p{font-size:6.2px;line-height:11.8px;margin-top:14px;text-align:justify}
.half--dark p+p{margin-top:10px}

/* support + about */
.support{background:#fff}
.page--a .support{height:573px}
.page--b .support{height:587px}
.support .title{top:48px}
.svc{position:absolute;top:87px;width:232px}
.svc-photo{height:131px}
.svc-photo--hands{background:linear-gradient(135deg,#cfd6de,#e7e9ec 40%,#b9a08a 70%,#8a99a8)}
.svc-photo--room{background:linear-gradient(135deg,#3a3f46,#8a9aa8 45%,#5e7a5a 75%,#2f353b)}
.svc-card{position:relative;margin:-17px 9px 0;height:105px;background:#fff;box-shadow:0 1px 6px rgba(0,0,0,.12);text-align:center;padding:13px 12px 0}
.svc-card h4{font-size:7.5px;font-weight:700;color:#111}
.svc-card p{font-size:6.2px;line-height:11.8px;color:var(--muted);margin-top:6px}
.about-mark{position:absolute;left:78px;top:368px;width:185px;height:170px;border-radius:50%;background:radial-gradient(circle at 40% 40%,#d6e6f3,#9fbfd9 60%,#e9f1f7)}
.about{position:absolute;left:296px;top:341px;width:242px}
.about h2{font-family:"Ubuntu",sans-serif;font-weight:500;font-size:18px;color:var(--ink)}
.about h2 b{color:var(--blue);font-weight:500}
.about p{font-size:6.4px;line-height:13.4px;color:var(--muted);margin-top:9px}
.about h5{font-size:6.4px;font-weight:700;color:#222;margin-top:9px}
.ticks{list-style:none;margin-top:7px}
.ticks li{display:flex;align-items:center;gap:6px;font-size:6.2px;color:var(--muted);height:13.5px}
.ticks li::before{content:"";width:5px;height:5px;border-radius:50%;background:var(--blue)}

/* contact */
.contact{color:#fff}
.page--a .contact{height:320px}
.page--b .contact{height:299px;background:var(--ink)}
.contact-curve{position:absolute;left:0;top:0;width:594px;height:60px}
.page--a .contact-body{position:absolute;left:0;top:45px;width:594px;height:275px;background:var(--ink)}
.page--b .contact-body{position:absolute;left:0;top:0;width:594px;height:299px}
.contact .title{color:#fff}
.page--a .contact .title{top:21px}
.page--b .contact .title{top:36px}
.info{position:absolute;left:92px;display:flex}
.page--a .info{top:55px}
.page--b .info{top:70px}
.info-item{display:flex;align-items:center;gap:7px;font-size:6.3px;line-height:10px}
.info-item .icon{width:31px;height:31px;border:2px solid #fff;flex:none}
.info-item .icon i{width:9px;height:9px;border-radius:50%;border:2px solid #fff}
.info-item strong{display:block;font-size:7px;font-weight:400}
.form{position:absolute;left:92px;width:408px}
.page--a .form{top:110px}
.page--b .form{top:124px}
.form .row{display:flex;gap:12px;margin-bottom:8px}
.field{height:20px;background:#fff;color:#555;font-size:6.2px;padding:6px 8px;flex:1}
.field--msg{height:42px}
.form .foot{display:flex;align-items:center;margin-top:16px;padding-left:15px;font-size:6.4px}
.check{width:8px;height:8px;background:#fff;margin-right:6px}
.captcha{width:22px;height:18px;margin-left:14px;border-radius:3px;background:linear-gradient(135deg,#4a90e2,#9bb8d3)}
.form .btn{width:52px;height:15px;margin-left:66px;border-radius:8px}

/* footer */
.footer{text-align:center;font-size:6.6px;color:#333}
.page--a .footer{height:72px;padding-top:21px}
.page--b .footer{height:76px;padding-top:22px}
.footer .social{display:flex;justify-content:center;gap:4px;margin-top:8px}
.footer .social span{width:16px;height:16px;border-radius:50%;border:1px solid #333}
</style>
</head>
<body>
<div class="stage">

<!-- ===== Version with curves ===== -->
<div class="page page--a">
  <header class="topbar">
    <div class="item" style="left:55px"><span class="dot"></span>Four Alder Square 12th Floor Easton, New York 10482</div>
    <div class="item" style="left:317px"><span class="dot"></span>info@harrowfield.us</div>
    <div class="item" style="left:436px"><span class="dot"></span>555.014.2270</div>
    <div class="social"><span></span><span></span><span></span></div>
  </header>
  <header class="nav">
    <div class="brand"><span class="mark"></span>harrowfield</div>
    <nav class="menu"><span class="active">Home</span><span>Services</span><span>About Us</span><span>Core Markets</span><span>News</span><span>Contact</span></nav>
    <span class="btn">&#8595; Download Brochure</span>
  </header>
  <section class="hero" role="img" aria-label="Photo of smiling shoppers with bags walking through a shopping mall">
    <div class="hero-panel">
      <h1>FIELD ANCHOR<br>SPECIAL EVENT SERVICES</h1>
      <p>CREATING SECURE ENVIRONMENTS.... SO YOU'RE IN CONTROL</p>
      <span class="btn">FREE CONSULTATION &#10140;</span>
    </div>
    <svg class="hero-curve" viewBox="0 0 594 90" preserveAspectRatio="none">
      <path d="M0 72 Q260 110 594 0 L594 90 L0 90Z" fill="#f3f3f3"/>
      <path d="M0 60 Q260 100 594 -8 L594 8 Q260 118 0 74Z" fill="#1a8fe3"/>
    </svg>
  </section>
  <section class="security">
    <h2 class="title title--rule" style="top:45px"><b>SECURITY</b> Technologies</h2>
    <div class="cards">
      <div class="card"><div class="icon"><i></i></div><h3>Rapid Video System Deployment</h3><p>Our cameras are designed to be deployed anywhere, even without power or Ethernet.</p></div>
      <div class="card"><div class="icon"><i></i></div><h3>Aerial Drone Surveillance</h3><p>Equipped with high resolution cameras &amp; thermal imaging capabilities, our drones provide a visual perspective that enhances overall situational awareness and supports damage</p></div>
      <div class="card"><div class="icon"><i></i></div><h3>Drone Detection Technology</h3><p>State-of-the-art drone detection technologies detect drone activity, pilot location, and classify the drone's characteristics and movement, facilitating early response and mitigation efforts.</p></div>
      <div class="card"><div class="icon"><i></i></div><h3>Gunfire Detection</h3><p>Our technology positively identifies gunfire, providing law enforcement and first responders with critical and accurate data.</p></div>
      <div class="card"><div class="icon"><i></i></div><h3>Real-time Weather Monitoring</h3><p>Our field anchor vehicle has live reporting curated remotely by a dedicated meteorologist.</p></div>
      <div class="card"><div class="icon"><i></i></div><h3>Social Media Monitoring</h3><p>Equipped to monitor various social media platforms, we use real-time intel to detect threats based on key words, entiment, subject matter and geo-location.</p></div>
    </div>
  </section>
  <section class="comm">
    <h2 class="title"><b>COMMUNICATION</b> Systems</h2>
    <div class="comm-list">
      <div class="comm-item"><div class="icon"><i></i></div><div><h4>LANDLINE TELEPHONE SERVICE</h4><p>Crisp, clear communications with landline handsets over cellular or satellite ensures intelligible audio.</p></div></div>
      <div class="comm-item"><div class="icon"><i></i></div><div><h4>TWO-WAY RADIOS AND CELLULAR PTT RADIOS</h4><p>Our two-way radios can be programmed to our clients' operating frequencies to expand their current radio communications into the field anchor. Our Cellular PTT radios expand the communications reach of your operation.</p></div></div>
      <div class="comm-item"><div class="icon"><i></i></div><div><h4>SATELLITE TV, RADIO, AND CELLULAR DATA</h4><p>Field anchor ensures continuous, high-speed, reliable data communications, coupled with live satellite TV and radio to maximize access to inbound information.</p></div></div>
    </div>
    <div class="comm-photo" role="img" aria-label="Photo of a smiling man working on a laptop"></div>
  </section>
  <section class="split">
    <div class="half half--dark">
      <div class="split-head"><span class="badge"><i></i></span><h2><b>SPECIAL EVENTS</b> Pose Special Challenges</h2></div>
      <p><strong>Managing security is stressful under the best of circumstances –</strong> planning for both the expected and unexpected is part of the job. But when you're tasked with securing a special event, emergency or disaster recovery, the "unexpected" takes on an additional dimension, pertaining not only to the security threats you may have to address but also to the uncertainty of security operations and technical infrastructure at your disposal.</p>
      <p>How do you quickly and economically set up a stable security operations center, equipped to gather and disseminate information, coordinate personnel and manage operations and response teams? Harrowfield Consulting can help.</p>
    </div>
    <div class="half half--blue">
      <div class="split-head"><span class="badge"><i></i></span><h2>HARROWFIELD'S FIELD ANCHOR<br>Special Event Services</h2></div>
      <p>Harrowfield's Field Anchor and Special Event Services provides your special event with the same level of technology and resources you'd expect at a permanent installation. With a comprehensive, highly reliable and redundant set of surveillance, monitoring and communication systems at your disposal, our state-of-the-art field anchor center is equipped with everything you need to execute a successful event. All systems are managed and monitored from within our Command Vehicle, furnished with large screen monitors and a robust software platform that rivals traditional Security Operations Centers. We also provide the knowledge and personnel to deploy those systems, including the site-wide placement of associated cameras, sensors, drones and other hardware and software necessary to provide widespread coverage.</p>
    </div>
  </section>
  <section class="support">
    <h2 class="title"><b>SUPPORT</b> Services</h2>
    <div class="svc" style="left:55px">
      <div class="svc-photo svc-photo--hands" role="img" aria-label="Photo of hands using a phone over a laptop with network graphics"></div>
      <div class="svc-card"><h4>SUPPORT SERVICES</h4><p>Our highly knowledgeable technical staff ensures that the technology aboard the field anchor is expressly programmed and deployed for each event to maximize its effectiveness.</p></div>
    </div>
    <div class="svc" style="left:306px">
      <div class="svc-photo svc-photo--room" role="img" aria-label="Photo of a control room with video wall and map displays"></div>
      <div class="svc-card"><h4>SEASONED SECURITY PROFESSIONALS</h4><p>Don't have a professional staff to plan and operate the security of your event? Harrowfield's professional staff holds decades of experience as first responders and possess a deep knowledge of special event planning, security operations and response and recovery</p></div>
    </div>
    <div class="about-mark" role="img" aria-label="Large brand decoration"></div>
    <div class="about">
      <h2><b>ABOUT</b> Harrowfield Consulting</h2>
      <p>Harrowfield Consulting is a team of seasoned security professionals with backgrounds in security management, law enforcement, emergency services and security technology. Put our expertise and experience to work for you!</p>
      <h5>Harrowfield employees hold various certifications and licenses, including:</h5>
      <ul class="ticks"><li>FAA Part 107 – Certified Drone Pilot</li><li>PSP – Physical Security Professional</li><li>CPP – Certified Protection Professional</li><li>CPOI – Certified Protection Officer Instructor</li><li>PE – Professional Engineer</li></ul>
    </div>
  </section>
  <section class="contact">
    <svg class="contact-curve" viewBox="0 0 594 60" preserveAspectRatio="none">
      <path d="M0 46 Q300 -20 594 44 L594 60 L0 60Z" fill="#1c1c1e"/>
      <path d="M0 30 Q300 -30 594 30 L594 44 Q300 -14 0 50Z" fill="#1a8fe3"/>
    </svg>
    <div class="contact-body">
      <h2 class="title"><b>CONTACT</b> Us</h2>
      <div class="info">
        <div class="info-item" style="width:162px"><span class="icon"><i></i></span><div><strong>Address:</strong>Four Alder Square 12th Floor<br>Easton, New York 10482</div></div>
        <div class="info-item" style="width:122px"><span class="icon"><i></i></span><div><strong>Phone</strong>555.014.2270</div></div>
        <div class="info-item"><span class="icon"><i></i></span><div><strong>Email:</strong>info@harrowfield.us</div></div>
      </div>
      <div class="form">
        <div class="row"><span class="field">Name</span><span class="field">Email</span></div>
        <div class="row"><span class="field">Phone</span><span class="field">subjects</span></div>
        <div class="row"><span class="field field--msg">Message</span></div>
        <div class="foot"><span class="check"></span>I'm not a Robot<span class="captcha" role="img" aria-label="Captcha badge"></span><span class="btn">SUBMIT</span></div>
      </div>
    </div>
  </section>
  <footer class="footer">
    Copyrights © The Company name 2020 | Allrights Reserved
    <div class="social"><span></span><span></span><span></span><span></span></div>
  </footer>
</div>

<!-- ===== Version without curves ===== -->
<div class="page page--b">
  <header class="topbar">
    <div class="item" style="left:55px"><span class="dot"></span>Four Alder Square 12th Floor Easton, New York 10482</div>
    <div class="item" style="left:317px"><span class="dot"></span>info@harrowfield.us</div>
    <div class="item" style="left:436px"><span class="dot"></span>555.014.2270</div>
    <div class="social"><span></span><span></span><span></span></div>
  </header>
  <header class="nav">
    <div class="brand"><span class="mark"></span>harrowfield</div>
    <nav class="menu"><span class="active">Home</span><span>Services</span><span>About Us</span><span>Core Markets</span><span>News</span><span>Contact</span></nav>
    <span class="btn">&#8595; Download Brochure</span>
  </header>
  <section class="hero" role="img" aria-label="Photo of smiling shoppers with bags walking through a shopping mall">
    <div class="hero-panel">
      <h1>FIELD ANCHOR<br>SPECIAL EVENT SERVICES</h1>
      <p>CREATING SECURE ENVIRONMENTS.... SO YOU'RE IN CONTROL</p>
      <span class="btn">FREE CONSULTATION &#10140;</span>
    </div>
  </section>
  <section class="security">
    <h2 class="title title--rule" style="top:52px"><b>SECURITY</b> Technologies</h2>
    <div class="cards" style="top:101px">
      <div class="card"><div class="icon"><i></i></div><h3>Rapid Video System Deployment</h3><p>Our cameras are designed to be deployed anywhere, even without power or Ethernet.</p></div>
      <div class="card"><div class="icon"><i></i></div><h3>Aerial Drone Surveillance</h3><p>Equipped with high resolution cameras &amp; thermal imaging capabilities, our drones provide a visual perspective that enhances overall situational awareness and supports damage</p></div>
      <div class="card"><div class="icon"><i></i></div><h3>Drone Detection Technology</h3><p>State-of-the-art drone detection technologies detect drone activity, pilot location, and classify the drone's characteristics and movement, facilitating early response and mitigation efforts.</p></div>
      <div class="card"><div class="icon"><i></i></div><h3>Gunfire Detection</h3><p>Our technology positively identifies gunfire, providing law enforcement and first responders with critical and accurate data.</p></div>
      <div class="card"><div class="icon"><i></i></div><h3>Real-time Weather Monitoring</h3><p>Our field anchor vehicle has live reporting curated remotely by a dedicated meteorologist.</p></div>
      <div class="card"><div class="icon"><i></i></div><h3>Social Media Monitoring</h3><p>Equipped to monitor various social media platforms, we use real-time intel to detect threats based on key words, entiment, subject matter and geo-location.</p></div>
    </div>
  </section>
  <section class="comm">
    <h2 class="title"><b>COMMUNICATION</b> Systems</h2>
    <div class="comm-list">
      <div class="comm-item"><div class="icon"><i></i></div><div><h4>LANDLINE TELEPHONE SERVICE</h4><p>Crisp, clear communications with landline handsets over cellular or satellite ensures intelligible audio.</p></div></div>
      <div class="comm-item"><div class="icon"><i></i></div><div><h4>TWO-WAY RADIOS AND CELLULAR PTT RADIOS</h4><p>Our two-way radios can be programmed to our clients' operating frequencies to expand their current radio communications into the field anchor. Our Cellular PTT radios expand the communications reach of your operation.</p></div></div>
      <div class="comm-item"><div class="icon"><i></i></div><div><h4>SATELLITE TV, RADIO, AND CELLULAR DATA</h4><p>Field anchor ensures continuous, high-speed, reliable data communications, coupled with live satellite TV and radio to maximize access to inbound information.</p></div></div>
    </div>
    <div class="comm-photo" role="img" aria-label="Photo of a smiling man working on a laptop"></div>
  </section>
  <section class="split">
    <div class="half half--dark">
      <div class="split-head"><span class="badge"><i></i></span><h2><b>SPECIAL EVENTS</b> Pose Special Challenges</h2></div>
      <p><strong>Managing security is stressful under the best of circumstances –</strong> planning for both the expected and unexpected is part of the job. But when you're tasked with securing a special event, emergency or disaster recovery, the "unexpected" takes on an additional dimension, pertaining not only to the security threats you may have to address but also to the uncertainty of security operations and technical infrastructure at your disposal.</p>
      <p>How do you quickly and economically set up a stable security operations center, equipped to gather and disseminate information, coordinate personnel and manage operations and response teams? Harrowfield Consulting can help.</p>
    </div>
    <div class="half half--blue">
      <div class="split-head"><span class="badge"><i></i></span><h2>HARROWFIELD'S FIELD ANCHOR<br>Special Event Services</h2></div>
      <p>Harrowfield's Field Anchor and Special Event Services provides your special event with the same level of technology and resources you'd expect at a permanent installation. With a comprehensive, highly reliable and redundant set of surveillance, monitoring and communication systems at your disposal, our state-of-the-art field anchor center is equipped with everything you need to execute a successful event. All systems are managed and monitored from within our Command Vehicle, furnished with large screen monitors and a robust software platform that rivals traditional Security Operations Centers. We also provide the knowledge and personnel to deploy those systems, including the site-wide placement of associated cameras, sensors, drones and other hardware and software necessary to provide widespread coverage.</p>
    </div>
  </section>
  <section class="support">
    <h2 class="title"><b>SUPPORT</b> Services</h2>
    <div class="svc" style="left:55px">
      <div class="svc-photo svc-photo--hands" role="img" aria-label="Photo of hands using a phone over a laptop with network graphics"></div>
      <div class="svc-card"><h4>SUPPORT SERVICES</h4><p>Our highly knowledgeable technical staff ensures that the technology aboard the field anchor is expressly programmed and deployed for each event to maximize its effectiveness.</p></div>
    </div>
    <div class="svc" style="left:306px">
      <div class="svc-photo svc-photo--room" role="img" aria-label="Photo of a control room with video wall and map displays"></div>
      <div class="svc-card"><h4>SEASONED SECURITY PROFESSIONALS</h4><p>Don't have a professional staff to plan and operate the security of your event? Harrowfield's professional staff holds decades of experience as first responders and possess a deep knowledge of special event planning, security operations and response and recovery</p></div>
    </div>
    <div class="about-mark" style="top:378px" role="img" aria-label="Large brand decoration"></div>
    <div class="about" style="top:341px">
      <h2><b>ABOUT</b> Harrowfield Consulting</h2>
      <p>Harrowfield Consulting is a team of seasoned security professionals with backgrounds in security management, law enforcement, emergency services and security technology. Put our expertise and experience to work for you!</p>
      <h5>Harrowfield employees hold various certifications and licenses, including:</h5>
      <ul class="ticks"><li>FAA Part 107 – Certified Drone Pilot</li><li>PSP – Physical Security Professional</li><li>CPP – Certified Protection Professional</li><li>CPOI – Certified Protection Officer Instructor</li><li>PE – Professional Engineer</li></ul>
    </div>
  </section>
  <section class="contact">
    <div class="contact-body">
      <h2 class="title"><b>CONTACT</b> Us</h2>
      <div class="info">
        <div class="info-item" style="width:162px"><span class="icon"><i></i></span><div><strong>Address:</strong>Four Alder Square 12th Floor<br>Easton, New York 10482</div></div>
        <div class="info-item" style="width:122px"><span class="icon"><i></i></span><div><strong>Phone</strong>555.014.2270</div></div>
        <div class="info-item"><span class="icon"><i></i></span><div><strong>Email:</strong>info@harrowfield.us</div></div>
      </div>
      <div class="form">
        <div class="row"><span class="field">Name</span><span class="field">Email</span></div>
        <div class="row"><span class="field">Phone</span><span class="field">subjects</span></div>
        <div class="row"><span class="field field--msg">Message</span></div>
        <div class="foot"><span class="check"></span>I'm not a Robot<span class="captcha" role="img" aria-label="Captcha badge"></span><span class="btn">SUBMIT</span></div>
      </div>
    </div>
  </section>
  <footer class="footer">
    Copyrights © The Company name 2020 | Allrights Reserved
    <div class="social"><span></span><span></span><span></span><span></span></div>
  </footer>
</div>

</div>
</body>
</html>
```